Business Card Design for Training Business

Clear Path Coaching is a new business that delivers training and other services with a focus on topics related to mental health and wellbeing, for example, Wellmind Response Course, Resilience etc. We have a strong focus on evidence-based psychology and neuroscience. I have a logo which I will upload with the brief, so please consider colours that work well with the logo.
Target Market(s)
Adults, workplaces (particularly government and not-for-profits)
Industry/Entity Type
Business
Contact Information for Business Card
Head Strong TrainingSamantha SellwoodDirector0438 770 850sam@headstrongtraining.com.auwww.headstrongtraining.com.au

```html
<!DOCTYPE html>
<html lang="en">
<head>
<meta charset="utf-8">
<title>Clear Path Coaching – Business Card</title>
<link rel="stylesheet" href="https://fonts.googleapis.com/css2?family=Questrial&family=Lato:wght@400&display=swap">
<style>
  :root {
    --teal: #22b8bd;
    --teal-deep: #1fb2b8;
    --card-white: #f7f7f7;
    --ink: #4a4a4a;
    --ink-soft: #6b6b6b;
    --backdrop: #2f2f2f;
    --white: #ffffff;
  }
  * { margin: 0; padding: 0; box-sizing: border-box; }
  html, body {
    width: 1200px;
    height: 750px;
    overflow: hidden;
    background: var(--backdrop);
  }
  .canvas {
    position: relative;
    width: 1200px;
    height: 750px;
  }
  .card {
    position: absolute;
    left: 371px;
    width: 461px;
    height: 262px;
    border-radius: 12px;
    overflow: hidden;
  }
  .card--front { top: 106px; background: var(--card-white); }
  .card--back { top: 387px; background: var(--teal); }

  .brand-tab {
    position: absolute;
    left: 331px;
    top: 0;
    width: 62px;
    height: 38px;
    background: var(--teal);
  }
  .brand-mark {
    position: absolute;
    left: 331px;
    top: 20px;
  }
  .brand-name {
    position: absolute;
    right: 21px;
    top: 98px;
    font-family: "Questrial", sans-serif;
    font-size: 15px;
    letter-spacing: 2px;
    color: var(--ink-soft);
    white-space: nowrap;
  }

  .name-accent {
    position: absolute;
    left: 0;
    top: 159px;
    width: 8px;
    height: 33px;
    background: var(--teal);
  }
  .person-name {
    position: absolute;
    left: 23px;
    top: 157px;
    font-family: "Questrial", sans-serif;
    font-size: 19px;
    color: var(--teal);
    white-space: nowrap;
  }
  .person-role {
    position: absolute;
    left: 24px;
    top: 179px;
    font-family: "Questrial", sans-serif;
    font-size: 13px;
    color: var(--ink);
  }
  .role-rule {
    position: absolute;
    left: 79px;
    top: 187px;
    width: 360px;
    height: 1px;
    background: var(--teal);
  }
  .contact {
    position: absolute;
    font-family: "Lato", sans-serif;
    font-size: 12px;
    color: var(--ink);
    white-space: nowrap;
  }
  .contact--phone { left: 23px; top: 208px; }
  .contact--phone .label { color: var(--teal); }
  .contact--email { left: 23px; top: 226px; font-family: "Questrial", sans-serif; }
  .contact--web { right: 22px; top: 226px; font-family: "Questrial", sans-serif; }

  .back-mark {
    position: absolute;
    left: 185px;
    top: 62px;
  }
  .back-name {
    position: absolute;
    left: 0;
    width: 100%;
    top: 166px;
    text-align: center;
    font-family: "Questrial", sans-serif;
    font-size: 14px;
    letter-spacing: 2px;
    color: var(--white);
  }
  .back-web {
    position: absolute;
    left: 0;
    width: 100%;
    top: 227px;
    text-align: center;
    font-family: "Questrial", sans-serif;
    font-size: 13px;
    color: var(--white);
  }
</style>
</head>
<body>
<main class="canvas">
  <section class="card card--front" aria-label="Business card front">
    <div class="brand-tab"></div>
    <svg class="brand-mark" width="62" height="62" viewBox="0 0 62 62" aria-hidden="true">
      <circle cx="31" cy="31" r="29" fill="var(--card-white)" stroke="var(--teal)" stroke-width="2"/>
    </svg>
    <div class="brand-name">CLEAR PATH COACHING</div>

    <div class="name-accent"></div>
    <div class="person-name">Rebecca Tanfield</div>
    <div class="person-role">Director</div>
    <div class="role-rule"></div>

    <div class="contact contact--phone"><span class="label">P:</span> 0491 362 517</div>
    <div class="contact contact--email">bec@clearpathcoaching.example.au</div>
    <div class="contact contact--web">www.clearpathcoaching.example.au</div>
  </section>

  <section class="card card--back" aria-label="Business card back">
    <svg class="back-mark" width="90" height="90" viewBox="0 0 90 90" aria-hidden="true">
      <circle cx="45" cy="45" r="43" fill="none" stroke="var(--white)" stroke-width="2"/>
    </svg>
    <div class="back-name">CLEAR PATH COACHING</div>
    <div class="back-web">www.clearpathcoaching.example.au</div>
  </section>
</main>
</body>
</html>
```